We need a web page design for a new company called "Brambel". We provide an innovative music sharing mobile application that allows music listeners to share their music without paying for a monthly subscription. We would like to incorporate the attached logo and color scheme. The final design should communicate music gifting and sharing.

Industry/Entity Type

It Company

```html
<!DOCTYPE html>
<html lang="en">
<head>
<meta charset="utf-8">
<title>Brambel</title>
<link href="https://fonts.googleapis.com/css2?family=Roboto:ital,wght@0,400;0,500;0,700;1,700&family=Lato:wght@400;700&display=swap" rel="stylesheet">
<style>
:root{
  --green:#63a80f;
  --green-light:#8cc043;
  --green-dark:#4f8a0a;
  --orange:#f39200;
  --ink:#333;
  --grey:#9a9a9a;
  --cream:#ebe8dc;
  --footer:#363636;
  --footer-bottom:#262626;
  --white:#fff;
}
*{box-sizing:border-box;margin:0;padding:0}
html,body{width:821px;height:1200px;overflow:hidden;background:var(--white)}
body{position:relative;font-family:"Roboto",Arial,sans-serif;color:var(--ink)}
.abs{position:absolute}

/* header */
.site-header{left:0;top:0;width:821px;height:60px;background:var(--green)}
.brand{left:120px;top:15px;display:flex;align-items:center;gap:6px}
.brand-dot{width:30px;height:30px;border-radius:50%;background:var(--white)}
.brand-name{font-family:"Lato",sans-serif;font-weight:700;font-size:29px;color:var(--white);line-height:1}
.main-nav{left:379px;top:0;height:60px;display:flex}
.main-nav a{display:block;height:60px;line-height:78px;padding:0 13px;font-size:9px;font-weight:700;color:var(--white);text-decoration:none}
.main-nav a.active{background:var(--white);color:var(--ink);padding:0 10px;margin-right:5px}
.account{left:680px;top:13px;font-size:8px;color:var(--white);font-weight:500}

/* hero */
.hero{left:0;top:60px;width:821px;height:264px;background:linear-gradient(100deg,#7a4a2a 0%,#d98a3c 25%,#c7692b 45%,#e8a85a 60%,#3d5e95 80%,#c9543b 100%)}
.hero-card{left:566px;top:126px;width:173px;height:96px;background:rgba(255,255,255,.55)}
.hero-badge{left:627px;top:104px;width:50px;height:50px;border-radius:50%;background:var(--green);border:3px solid var(--white)}
.hero-title{left:566px;top:155px;width:173px;text-align:center;font-family:"Lato",sans-serif;font-weight:700;font-size:20px;color:#333}
.hero-controls{left:607px;top:193px;display:flex;height:18px}
.hero-controls span{display:block;height:18px;line-height:18px;font-size:8px;color:var(--white);text-align:center}
.hero-controls .arr{width:18px;background:var(--green)}
.hero-controls .more{width:56px;background:#555}

/* features */
.features{left:113px;top:324px;width:640px;height:129px;display:flex}
.feature{position:relative;width:160px;height:129px;text-align:center;color:var(--white)}
.feature:nth-child(odd){background:var(--green)}
.feature:nth-child(even){background:var(--green-light)}
.feature h3{position:absolute;top:50px;width:100%;font-size:12.5px;font-weight:500}
.feature p{position:absolute;top:69px;left:14px;right:14px;font-size:9px;line-height:11.5px}
.feature .plus{position:absolute;left:70px;bottom:0;width:20px;height:19px;background:var(--orange);border:2px solid var(--white);border-bottom:0}
.feature .plus::before,.feature .plus::after{content:"";position:absolute;background:var(--white)}
.feature .plus::before{left:7px;top:3px;width:2px;height:12px}
.feature .plus::after{left:2px;top:8px;width:12px;height:2px}
.feature-icon{position:absolute;top:-42px;left:38px;width:84px;height:84px;border-radius:50%;background:var(--white);border:3px solid var(--green);display:flex;align-items:center;justify-content:center}

/* section headings */
.section-title{font-size:14px;color:#333;padding-left:4px;border-left:2px solid var(--green);line-height:15px}
.pager{display:flex;gap:1px}
.pager span{width:16px;height:16px;line-height:16px;text-align:center;font-size:10px;color:var(--white)}

/* trending */
.track{top:510px;width:147px}
.cover{width:147px;height:147px;border:5px solid var(--green)}
.cover.hot{border-color:var(--orange)}
.cover div{width:100%;height:100%}
.track p{margin-top:6px;font-size:8.5px;font-weight:700;font-style:italic;color:#333}
.track .btns{display:flex;justify-content:space-between;margin-top:6px;padding:0 2px 7px;border-bottom:2px solid var(--green)}
.btn{font-size:8.5px;color:var(--white);height:14px;line-height:14px;text-align:center}
.btn.share{background:var(--green);width:40px}
.btn.gift{background:var(--grey);width:40px}

/* cta */
.cta{left:113px;top:726px;width:640px;height:59px;background:var(--cream);border:1px solid #d5d1c0}
.cta p{position:absolute;left:6px;top:21px;font-size:14px;color:#333}
.cta .signup{position:absolute;left:543px;top:15px;width:88px;height:27px;line-height:27px;background:var(--green);color:var(--white);font-size:10px;font-weight:700;text-align:center}

/* categories */
.read-more{left:684px;top:815px;width:67px;height:20px;line-height:20px;background:var(--orange);font-size:8.5px;font-weight:700;color:#333;text-align:center}
.cat{width:80px;height:20px;display:flex;align-items:center;border-bottom:1px solid #eee;font-size:9px;color:#333}
.cat.on{color:var(--green)}
.cat i{width:11px;height:11px;border-radius:50%;background:#c9c9c9;margin-right:5px;border:3px solid #e3e3e3}
.cat b{margin-left:auto;width:8px;height:8px;background:var(--green)}

/* footer */
.site-footer{left:0;top:1038px;width:821px;height:134px;background:var(--footer);border-top:3px solid var(--green);color:var(--white)}
.foot-h{font-size:13px;color:var(--white);padding-bottom:4px;border-bottom:1px solid #555;font-weight:400}
.quick li{list-style:none;font-size:9px;line-height:14.5px}
.quick li::before{content:"›";margin-right:6px}
.news-item{display:flex;gap:7px;font-size:8.5px;line-height:10px}
.news-item .date{width:25px;text-align:center;font-weight:700}
.news-item .date b{display:block;background:var(--green);height:13px;line-height:13px;font-size:9px}
.news-item .date span{display:block;background:var(--white);color:#333;font-size:7px;height:10px;line-height:10px}
.email{width:142px;height:17px;background:var(--white);font-size:7px;font-style:italic;color:#888;line-height:17px;padding-left:4px}
.subscribe{width:72px;height:19px;line-height:19px;background:var(--green);font-size:10px;font-weight:700;text-align:center}
.social{display:flex;gap:7px}
.social span{width:16px;height:16px;border-radius:50%;background:#555}
.copyright{left:0;top:1172px;width:821px;height:28px;background:var(--footer-bottom);color:#ddd;font-size:8.5px;line-height:28px;text-align:center}
</style>
</head>
<body>

<header class="abs site-header">
  <div class="abs brand"><span class="brand-dot"></span><span class="brand-name">Brambel</span></div>
  <nav class="abs main-nav">
    <a class="active" href="#">HOME</a><a href="#">SERVICES</a><a href="#">TIMETABLE</a><a href="#">NEWS</a><a href="#">FEATURES</a><a href="#">CONTACTS</a>
  </nav>
  <div class="abs account">LOGIN &nbsp;| &nbsp;SIGNUP</div>
</header>

<section class="abs hero" role="img" aria-label="Photo of a smiling woman listening to headphones against blurred colourful city lights"></section>
<div class="abs hero-card"></div>
<div class="abs hero-badge"></div>
<div class="abs hero-title">Brambel</div>
<div class="abs hero-controls"><span class="arr">‹</span><span class="more">READ MORE</span><span class="arr">›</span></div>

<section class="abs features">
  <div class="feature">
    <div class="feature-icon"><svg width="44" height="44" viewBox="0 0 44 44"><path d="M16 8 L36 4 V30" fill="none" stroke="#f39200" stroke-width="4"/><path d="M16 8 V34" stroke="#f39200" stroke-width="4"/><ellipse cx="11" cy="34" rx="6" ry="5" fill="#f39200"/><ellipse cx="31" cy="30" rx="6" ry="5" fill="#f39200"/></svg></div>
    <h3>UPLOAD MUSIC &amp; AUDIO</h3><p>Lorem Ipsum is simply dummy text of the printing.</p><span class="plus"></span>
  </div>
  <div class="feature">
    <div class="feature-icon"><svg width="46" height="46" viewBox="0 0 46 46"><path d="M7 28 V23 a16 16 0 0 1 32 0 V28" fill="none" stroke="#f39200" stroke-width="4"/><rect x="5" y="25" width="10" height="16" rx="4" fill="#f39200"/><rect x="31" y="25" width="10" height="16" rx="4" fill="#f39200"/></svg></div>
    <h3>LISTEN &amp; DISCOVER</h3><p>Lorem Ipsum is simply dummy text of the printing fdsjoid.</p><span class="plus"></span>
  </div>
  <div class="feature">
    <div class="feature-icon"><svg width="46" height="46" viewBox="0 0 46 46"><circle cx="20" cy="14" r="8" fill="#f39200"/><path d="M6 38 a14 12 0 0 1 28 0 Z" fill="#f39200"/><circle cx="33" cy="22" r="6" fill="#f39200"/><path d="M26 40 a9 9 0 0 1 18 0 Z" fill="#f39200"/></svg></div>
    <h3>CONNECT</h3><p>Lorem Ipsum is simply dummy text of the printing.</p><span class="plus"></span>
  </div>
  <div class="feature">
    <div class="feature-icon"><svg width="46" height="46" viewBox="0 0 46 46"><g stroke="#f39200" stroke-width="3"><line x1="23" y1="23" x2="10" y2="10"/><line x1="23" y1="23" x2="37" y2="12"/><line x1="23" y1="23" x2="9" y2="36"/><line x1="23" y1="23" x2="37" y2="36"/></g><g fill="#f39200"><circle cx="23" cy="23" r="7"/><circle cx="10" cy="10" r="5"/><circle cx="37" cy="12" r="5"/><circle cx="9" cy="36" r="5"/><circle cx="37" cy="36" r="5"/></g></svg></div>
    <h3>SHARE</h3><p>Lorem Ipsum is simply dummy text of the printing fdsjoid.</p><span class="plus"></span>
  </div>
</section>

<h2 class="abs section-title" style="left:113px;top:483px;font-weight:400">TRENDING MUSIC &amp; AUDIO</h2>
<div class="abs pager" style="left:719px;top:482px"><span style="background:#ccc">‹</span><span style="background:var(--green)">›</span></div>

<article class="abs track" style="left:113px">
  <div class="cover"><div role="img" aria-label="Album cover artwork, black and white portrait" style="background:linear-gradient(160deg,#555,#1a1a1a)"></div></div>
  <p>Lorem ipsum dolor sfgjit rem Ipsumis</p>
  <div class="btns"><span class="btn share">SHARE</span><span class="btn gift">GIFT</span></div>
</article>
<article class="abs track" style="left:277px">
  <div class="cover hot"><div role="img" aria-label="Album cover artwork, copper lettering on black" style="background:radial-gradient(circle,#a0553a 0%,#2a1a14 60%,#111 100%)"></div></div>
  <p>Lorem ipsum dolor sfgjit rem Ipsumis</p>
  <div class="btns"><span class="btn share">SHARE</span><span class="btn gift">GIFT</span></div>
</article>
<article class="abs track" style="left:440px">
  <div class="cover"><div role="img" aria-label="Album cover artwork, bold pink graphic on white" style="background:linear-gradient(135deg,#e0248f 0%,#f5c6df 55%,#e0248f 100%)"></div></div>
  <p>Lorem ipsum dolor sfgjit rem Ipsumis</p>
  <div class="btns"><span class="btn share">SHARE</span><span class="btn gift">GIFT</span></div>
</article>
<article class="abs track" style="left:604px">
  <div class="cover"><div role="img" aria-label="Album cover artwork, dark golden fantasy scene" style="background:radial-gradient(circle at 50% 40%,#b08a3a,#4a3412 70%,#22180a)"></div></div>
  <p>Lorem ipsum dolor sfgjit rem Ipsumis</p>
  <div class="btns"><span class="btn share">SHARE</span><span class="btn gift">GIFT</span></div>
</article>

<section class="abs cta">
  <p>So are you ready to discover new music and sounds and share them with the world?</p>
  <span class="signup">SIGN UP NOW</span>
</section>

<h2 class="abs section-title" style="left:113px;top:817px;font-weight:400">MUSIC CATEGORIES</h2>
<span class="abs read-more">READ MORE</span>

<div class="abs" style="left:113px;top:855px;width:640px;display:grid;grid-template-columns:106px 109px 109px 113px 116px 87px;row-gap:6.6px">
  <div class="cat on"><i></i>Acoustic<b></b></div><div class="cat"><i></i>Acoustic<b></b></div><div class="cat"><i></i>Acoustic<b></b></div><div class="cat"><i></i>Acoustic<b></b></div><div class="cat"><i></i>Acoustic<b></b></div><div class="cat"><i></i>Acoustic<b></b></div>
  <div class="cat"><i></i>Music-Pack<b></b></div><div class="cat"><i></i>Music-Pack<b></b></div><div class="cat"><i></i>Music-Pack<b></b></div><div class="cat"><i></i>Music-Pack<b></b></div><div class="cat"><i></i>Music-Pack<b></b></div><div class="cat"><i></i>Music-Pack<b></b></div>
  <div class="cat"><i></i>Drum'n' Bass<b></b></div><div class="cat"><i></i>Drum'n' Bass<b></b></div><div class="cat"><i></i>Drum'n' Bass<b></b></div><div class="cat"><i></i>Drum'n' Bass<b></b></div><div class="cat"><i></i>Drum'n' Bass<b></b></div><div class="cat"><i></i>Drum'n' Bass<b></b></div>
  <div class="cat"><i></i>Alternative<b></b></div><div class="cat"><i></i>Alternative<b></b></div><div class="cat"><i></i>Alternative<b></b></div><div class="cat"><i></i>Alternative<b></b></div><div class="cat"><i></i>Alternative<b></b></div><div class="cat"><i></i>Alternative<b></b></div>
  <div class="cat"><i></i>Eurodance<b></b></div><div class="cat"><i></i>Eurodance<b></b></div><div class="cat"><i></i>Eurodance<b></b></div><div class="cat"><i></i>Eurodance<b></b></div><div class="cat"><i></i>Eurodance<b></b></div><div class="cat"><i></i>Eurodance<b></b></div>
  <div class="cat"><i></i>Ambient<b></b></div><div class="cat"><i></i>Ambient<b></b></div><div class="cat"><i></i>Ambient<b></b></div><div class="cat"><i></i>Ambient<b></b></div><div class="cat"><i></i>Ambient<b></b></div><div class="cat"><i></i>Ambient<b></b></div>
</div>

<footer class="abs site-footer">
  <div class="abs" style="left:113px;top:12px;width:95px">
    <h4 class="foot-h">Quick Links</h4>
    <ul class="quick" style="margin-top:4px"><li>Home</li><li>Services</li><li>Timetable</li><li>News</li><li>Features</li><li>Contact Us</li></ul>
  </div>
  <div class="abs" style="left:229px;top:12px;width:156px">
    <h4 class="foot-h">News Updates</h4>
    <div class="abs pager" style="left:133px;top:3px"><span style="background:var(--green);width:11px;height:11px;line-height:11px">‹</span><span style="background:var(--green);width:11px;height:11px;line-height:11px">›</span></div>
    <div class="news-item" style="margin-top:9px"><div class="date"><b>12</b><span>NOV</span></div><div><b>Vero eros accumsaet odio</b><br>quis nostrud exetiperj suscipit<br>nisl ut aliquip ex ea commod</div></div>
    <div class="news-item" style="margin-top:12px"><div class="date"><b>20</b><span>NOV</span></div><div><b>Vero eros accumsaet odio</b><br>quis nostrud exetiperj suscipit<br>nisl ut aliquip ex ea commod</div></div>
  </div>
  <div class="abs" style="left:430px;top:12px;width:146px">
    <h4 class="foot-h">Newsletter Sign Up</h4>
    <p style="font-size:8px;line-height:12px;margin-top:5px">Lorem ipsudolor sit coec adipiscing elitsite amet</p>
    <div class="email" style="margin-top:8px">Email Address</div>
    <div class="subscribe" style="margin-top:8px">SUBSCRIBE</div>
  </div>
  <div class="abs" style="left:604px;top:10px;width:1px;height:110px;background:#4a4a4a"></div>
  <div class="abs brand" style="left:622px;top:45px"><span class="brand-dot" style="width:24px;height:24px"></span><span class="brand-name" style="font-size:24px">Brambel</span></div>
  <div class="abs social" style="left:642px;top:95px"><span></span><span style="background:var(--green)"></span><span></span><span></span></div>
</footer>
<div class="abs copyright">© 2014 <b>BrambelMusic</b>. All Rights Reserved.</div>

</body>
</html>
```